KBT Business Cards

We require business cards for our business. We would like a matte black back to the card, with our logo centred in the middle. The front side of the card is open to design.

Target Market(s)

Clients looking for legal services (professional)

Industry/Entity Type

Legal

Contact Information for Business Card

Doran Kelbrath
Partner
Mobile: 0461 738 524
Email: doran@kbtlaw.co
Website: www.kbtlaw.co
Level 3, 118 Wendmore Street
Sydney NSW 2000

Font styles to use
Other font styles liked:
• Avenir

Colors
f04a50
ffffff
1b1b1b

Requirements
Must have
• Black back with logo included in the centre of the card.
• Our font is Avenir.

```html
<!DOCTYPE html>
<html lang="en">
<head>
<meta charset="utf-8">
<title>KBT Legal Business Cards</title>
<link rel="stylesheet" href="https://fonts.googleapis.com/css2?family=Montserrat:wght@400;500;600;700&family=Playfair+Display:ital,wght@1,700&display=swap">
<style>
  :root {
    --canvas: #d8d3cb;
    --card-dark: #1b1b1b;
    --card-mid: #262626;
    --accent: #d3245b;
    --white: #ffffff;
    --muted: #e6e6e6;
    --rule: rgba(211, 36, 91, 0.7);
  }
  * { margin: 0; padding: 0; box-sizing: border-box; }
  html, body {
    width: 1200px;
    height: 780px;
    overflow: hidden;
    background: var(--canvas);
    font-family: "Montserrat", Arial, sans-serif;
  }
  .stage {
    width: 1200px;
    height: 780px;
    display: flex;
    align-items: center;
    justify-content: center;
    gap: 90px;
  }
  .card {
    position: relative;
    width: 360px;
    height: 590px;
    border-radius: 4px;
    overflow: hidden;
    box-shadow: 0 18px 40px rgba(0, 0, 0, 0.25);
  }
  .card-texture {
    position: absolute;
    inset: 0;
    background: linear-gradient(160deg, var(--card-mid) 0%, var(--card-dark) 55%, #141414 100%);
  }
  .brand {
    position: relative;
    display: flex;
    align-items: center;
    gap: 14px;
  }
  .brand-square {
    width: 46px;
    height: 46px;
    background: var(--accent);
  }
  .brand-name {
    color: var(--white);
    font-weight: 600;
    font-size: 26px;
    letter-spacing: 0.08em;
    text-transform: uppercase;
    line-height: 1;
  }

  /* Front */
  .card-front .brand {
    justify-content: center;
    margin-top: 70px;
  }
  .contact {
    position: relative;
    text-align: center;
    margin-top: 62px;
    padding: 0 36px;
  }
  .contact-name {
    color: var(--accent);
    font-weight: 700;
    font-size: 22px;
    letter-spacing: 0.04em;
    text-transform: uppercase;
  }
  .contact-role {
    color: var(--white);
    font-weight: 400;
    font-size: 15px;
    margin-top: 4px;
  }
  .contact-rule {
    height: 1px;
    background: var(--rule);
    margin: 14px 0 10px;
  }
  .contact-label {
    font-family: "Playfair Display", Georgia, serif;
    font-style: italic;
    font-weight: 700;
    font-size: 12px;
    color: var(--accent);
  }
  .contact-value {
    color: var(--white);
    font-size: 16px;
    font-weight: 500;
    margin-top: 2px;
  }
  .contact-address {
    color: var(--muted);
    font-size: 15px;
    font-weight: 500;
    line-height: 1.5;
  }
  .web-band {
    position: absolute;
    left: 0;
    right: 0;
    bottom: 0;
    height: 86px;
    background: var(--accent);
    border-top: 4px solid var(--white);
    display: flex;
    align-items: center;
    justify-content: center;
  }
  .web-address {
    color: var(--white);
    font-size: 17px;
    font-weight: 500;
    letter-spacing: 0.14em;
  }

  /* Back */
  .card-back .brand {
    position: absolute;
    top: 50%;
    left: 50%;
    transform: translate(-50%, -50%);
  }
</style>
</head>
<body>
<main class="stage">
  <section class="card card-front" aria-label="Business card front">
    <div class="card-texture" role="img" aria-label="Dark background with faint tilted square tiles"></div>
    <div class="brand">
      <span class="brand-square"></span>
      <span class="brand-name">KBT Legal</span>
    </div>
    <div class="contact">
      <p class="contact-name">Doran Kelbrath</p>
      <p class="contact-role">Partner</p>
      <div class="contact-rule"></div>
      <p class="contact-label">Cell:</p>
      <p class="contact-value">0461 738 524</p>
      <div class="contact-rule"></div>
      <p class="contact-label">Email:</p>
      <p class="contact-value">doran@kbtlaw.co</p>
      <div class="contact-rule"></div>
      <p class="contact-address">Level 3, 118 Wendmore Street<br>Sydney NSW 2000</p>
    </div>
    <div class="web-band">
      <p class="web-address">www.kbtlaw.co</p>
    </div>
  </section>

  <section class="card card-back" aria-label="Business card back">
    <div class="card-texture" role="img" aria-label="Dark background with faint tilted square tiles"></div>
    <div class="brand">
      <span class="brand-square"></span>
      <span class="brand-name">KBT Legal</span>
    </div>
  </section>
</main>
</body>
</html>
```